Design a sleek menu for our new smoothie and snacks shop”Glee”

requiring a store drinks and snacks menu we would like to have a white background for the menu . I would like to have fruit watermarks like in our original design concept , For reference ,please refer to the pictures . The font and layout of the menu should be modern , simple but stylish and reflect a smoothie shop.
we will be proving the menu contents to input once we agree to the design concept .
here are the menu documents

smoothies

Regular 16oz £4.99 Large 20oz £5.99
substitute semi skim for any dairy free milks for .50p
add vegan protein or regular protein for .50p

Berry set go
mixed berries, banana, coconut yogurt, milk

Green Meadow
Spinach, avocado, matcha, banana, milk, agave

Power to the purple
Blueberries, banana, açai, coconut milk

Mango Monsoon
Mango, apple, strawberry, coconut milk, vanilla yogurt, agave

Go Ape Glee
Oats, banana, cinnamon, dates, almond butter

Caribbean Dream
Pineapple, spinach, banana, coconut milk

Mocha lotta
Oats, banana, cinnamon, cocoa, espresso, skim milk

Cocoa Banana
Oats, banana, cocoa, cinnamon, peanut butter , agave
*almond butter substitute is available

PB & J Day
Frozen berries, banana, peanut butter, maple syrup, coconut milk
*Spinach is optional

Strawberry Glee
Strawberries, banana, coconut milk, orange juice, agave

Kale Krush
Spinach, kale, pineapple, apple juice

Young Blood
Celery, lemon, apple

Berry Beautiful
Blueberries, banana, vanilla yogurt, soy milk, collagen protein, agave,

Shakes
Large 16oz £6
Add Protein for .50p

Avo Shake
Avocado, banana, skim milk, vanilla

Cocoa Shake
Avocado, cocoa powder, coconut milk, banana, maple syrup
*can substitute avocado with dairy free ice cream

Sweet Vegan
Dairy free vanilla Ice cream, banana, cocoa powder, coconut milk, agave

The last straw
Strawberry ,dates , dairy free ice cream, coconut milk, agave
*substitute dairy free ice cream for avocado

Caffeine frenzy
Espresso, banana, dairy free ice cream, cocoa powder, almond milk, agave

Berry Bunch
Oats, mixed berries, banana, dates ,soy milk, dairy free ice cream

Immune boosters
Regular 16 oz £6
Smoothie Bowl £5.50 * Available on a seasonal basis

The yellow one: Pineapple turmeric
Pineapple, banana, lemon, agave, ginger,tumeric,coconut water

The Red one : Citrus Berry Ginger
Orange, strawberry, lemon, ginger , almond milk

The Orange one : Citrus carrot
Grapefruit, clementine, carrot,mango,yogurt,lemon,tumeric

Teas
Regular £2
Green geisha
Breakfast blend
Lemon & ginger
Moroccan mint

Iced Frappé
* Substitute for non dairy for .50p
Regular £3.50
Cappuccino - expresso, milk, ice
Mocha- cocoa ,milk, ice
Strawberry's n cream- Strawberry,cream,ice
Mighty Matcha - Matcha, cream, ice
Vanilla Bean- Vanilla, cream, ice
Glee Sandwiches
£4.50

Avocado
Avocado , mozerella,tomatoe, pesto

Spicy Tuna
Tuna, Chilli peppers, mayo, salt, pepper

Tunacado
Tuna, avocado, mayo, salt, pepper

BLT
Turkey Rasher, lettuce, mayo, tomatoe

American Grilled Cheese
Mature Cheddar , wholewheat bread
*sourdough bread is optional

Yogurt
£3
Coconut ,Vanilla yogurt , banana, granola

Bowls
£4.50
+ protein=.50p

Acai Bowl
Acai, Raspberry,blueberry,banana,almond milk, granola
*Topping: granola and ½ banana sliced ,chia seeds

Cocoa Bowl
Cocoa,banana,peanut butter,almond milk
Toppings : chocolate granola, peanut butter ,chia seeds,1/2 banana sliced

Target Market(s)

any age , predominately ages 20+

Industry/Entity Type

food & drink

Colors

Designer to choose colors to be used in the design.

Requirements
Must have
• clean, modern concept
Nice to have
• white background, fruits in the background -animated or actual ones
Should not have
• no dark background concepts

```html
<!DOCTYPE html>
<html lang="en">
<head>
<meta charset="utf-8">
<title>Glee – Menu</title>
<link rel="stylesheet" href="https://fonts.googleapis.com/css2?family=Oswald:wght@500;600&family=Lato:wght@400;700;900&family=Alfa+Slab+One&family=Bebas+Neue&family=Mrs+Saint+Delafield&family=Lora:wght@400;700&display=swap">
<style>
:root{
  --pink:#cf2e62;
  --pink-soft:#f6c9d8;
  --pink-faint:#fbe6ee;
  --green:#6b9a33;
  --ink:#2a2a2a;
  --paper:#ffffff;
}
*{box-sizing:border-box;margin:0;padding:0}
html,body{width:900px;height:1200px;overflow:hidden;background:var(--paper)}
body{position:relative;font-family:'Lato',sans-serif;color:var(--ink)}
.abs{position:absolute}

.fruit-band{left:0;top:0;width:900px;height:230px;
  background:linear-gradient(180deg,var(--pink-faint) 0%,#fdf1f5 70%,rgba(255,255,255,0) 100%)}

.brand{left:374px;top:34px;width:160px;height:160px;border-radius:50%;background:#3a3a3a;
  display:flex;align-items:center;justify-content:center}
.brand-name{font-family:'Lato',sans-serif;font-weight:900;font-size:46px;color:#ffffff;letter-spacing:1px}

.panel{border:1.5px solid var(--pink-soft);background:rgba(255,255,255,.92)}

/* Smoothies */
.smoothies{left:40px;top:176px;width:409px;height:632px;padding:0 0 0 20px}
.smoothies-title{font-family:'Oswald',sans-serif;font-weight:600;font-size:42px;color:var(--pink);text-align:center;margin-top:16px;line-height:1;letter-spacing:.5px}
.smoothies-price{font-family:'Lato',sans-serif;font-weight:900;font-size:9.5px;color:var(--pink);text-align:center;letter-spacing:1px;margin-top:5px}
.smoothies-note{font-weight:700;font-size:7.8px;color:var(--pink);text-align:center;letter-spacing:.6px;line-height:1.3;margin-top:9px}
.drink-list{margin-top:11px}
.drink{margin-bottom:4.5px}
.drink-name{font-weight:700;font-size:13.5px;color:var(--pink);text-transform:uppercase;line-height:17px;letter-spacing:.2px}
.drink-desc{font-size:12.4px;line-height:14.5px;padding-left:13px}
.small-note{font-size:7.5px;text-transform:uppercase}

/* Shakes */
.shakes{left:461px;top:175px;width:409px;height:309px}
.shakes-band{height:29px;background:repeating-linear-gradient(115deg,var(--pink) 0 3px,#e06a90 3px 5px);
  display:flex;align-items:center;justify-content:center}
.shakes-title{font-family:'Oswald',sans-serif;font-weight:600;font-size:17px;color:#fff;letter-spacing:1px}
.shakes-price{font-weight:900;font-size:9.5px;color:var(--pink);text-align:center;letter-spacing:1px;margin-top:9px}
.shake-grid{display:grid;grid-template-columns:1fr 1fr;column-gap:8px;padding:16px 10px 0 22px}
.shake{margin-bottom:10px}
.shake-name{font-family:'Oswald',sans-serif;font-weight:500;font-size:16px;color:var(--pink);text-transform:uppercase;line-height:19px}
.shake-desc{font-size:12.2px;line-height:13px}
.shake-desc .small-note{display:block;font-size:7.5px;line-height:9px;margin-top:2px;padding-left:3px}

/* Yogurt ring */
.yogurt{left:433px;top:497px;width:166px;height:166px;border-radius:50%;border:5px solid #d9487a;text-align:center;padding-top:52px}
.yogurt-name{font-family:'Oswald',sans-serif;font-weight:500;font-size:17px;color:var(--pink)}
.price{font-family:'Lora',serif;font-weight:700;font-size:12px}
.yogurt-desc{font-size:12px;line-height:13.5px;margin-top:4px}

/* Bowls */
.bowls{left:623px;top:515px;width:250px}
.bowls-title{font-family:'Oswald',sans-serif;font-weight:600;font-size:38px;color:var(--pink);line-height:1;letter-spacing:.5px}
.bowls-protein{font-family:'Lora',serif;font-weight:700;font-size:8px;margin-top:4px}
.bowl-name{font-family:'Oswald',sans-serif;font-weight:500;font-size:16px;color:var(--pink);text-transform:uppercase;margin-top:12px}
.bowl-desc{font-size:12px;line-height:13.5px;margin-top:5px}
.bowl-note{font-size:7.5px;line-height:9px;text-transform:uppercase;margin-top:3px}
.cocoa-bowl{left:500px;top:684px;width:380px}
.cocoa-bowl .bowl-name{margin-top:0}

/* Immune */
.immune{left:462px;top:791px;width:408px;height:186px}
.immune-title{font-family:'Alfa Slab One',serif;font-size:25px;color:var(--pink);padding:12px 0 0 16px;line-height:1;letter-spacing:1px}
.immune-price{font-family:'Oswald',sans-serif;font-weight:500;font-size:13px;color:var(--pink);padding-left:16px;letter-spacing:.8px}
.immune-note{font-size:7px;color:var(--pink);padding-left:16px;letter-spacing:.6px;text-transform:uppercase;border-bottom:1.5px solid var(--pink-soft);padding-bottom:4px}
.immune-list{padding:8px 0 0 16px}
.immune .drink{margin-bottom:2px}
.immune .drink-name{font-size:12.8px}
.immune .drink-desc{font-size:11.6px;padding-left:12px}

/* Sandwiches */
.sandwich-title{left:46px;top:845px;font-family:'Mrs Saint Delafield',cursive;font-size:76px;color:var(--green);line-height:1;white-space:nowrap}
.sandwich{width:125px}
.sandwich-name{font-family:'Oswald',sans-serif;font-weight:500;font-size:16px;color:var(--green);text-transform:uppercase;line-height:20px;white-space:nowrap}
.sandwich .price{margin-top:4px}
.sandwich-desc{font-size:12px;line-height:14px;margin-top:3px}
.sandwich-note{font-size:7.5px;margin-top:2px}

/* Teas */
.teas{left:458px;top:1003px;width:174px;height:132px;border:6px solid var(--green);border-bottom:none;border-radius:26px 26px 0 0;text-align:center;padding-top:10px}
.teas-title{font-family:'Bebas Neue',sans-serif;font-size:26px;color:var(--green);line-height:1}
.teas-price{font-family:'Lora',serif;font-weight:700;font-size:10px;letter-spacing:1px;margin:6px 0 5px}
.tea{font-family:'Bebas Neue',sans-serif;font-size:12px;line-height:14px;letter-spacing:.2px}

.frap{left:652px;top:1010px;width:210px}
.frap-head{display:flex;align-items:flex-start;gap:8px;border-bottom:1.5px dashed var(--green);padding-bottom:4px}
.frap-title{font-family:'Bebas Neue',sans-serif;font-size:28px;color:var(--green);line-height:1}
.frap-price{font-family:'Lora',serif;font-weight:700;font-size:9.5px;line-height:11px;letter-spacing:.6px}
.frap-grid{display:grid;grid-template-columns:105px 105px;margin-top:6px}
.frap-name{font-family:'Bebas Neue',sans-serif;font-size:13px;line-height:13px}
.frap-desc{font-family:'Lora',serif;font-size:10.5px;line-height:13px}
.baseline{left:444px;top:1133px;width:410px;border-top:1.5px dashed var(--green)}
</style>
</head>
<body>

<div class="abs fruit-band" role="img" aria-label="Soft pink line drawings of fruit: bananas, strawberries, pineapples, cherries, grapes and pears"></div>

<div class="abs brand"><span class="brand-name">Glee</span></div>

<section class="abs panel smoothies">
  <h2 class="smoothies-title">SMOOTHIES</h2>
  <p class="smoothies-price">REGULAR 16OZ £4.99 LARGE 20OZ £5.99</p>
  <p class="smoothies-note">SUBSTITUTE SEMI SKIM FOR ANY DAIRY FREE MILKS FOR .50P<br>ADD VEGAN PROTEIN OR REGULAR PROTEIN FOR .50P</p>
  <div class="drink-list">
    <div class="drink"><p class="drink-name">Berry Set Go</p><p class="drink-desc">Mixed berries, banana, coconut yogurt, milk</p></div>
    <div class="drink"><p class="drink-name">Green Meadow</p><p class="drink-desc">Spinach, avocado, matcha, banana, milk, agave</p></div>
    <div class="drink"><p class="drink-name">Power to the Purple</p><p class="drink-desc">Blueberries, banana, açai, coconut milk</p></div>
    <div class="drink"><p class="drink-name">Mango Monsoon</p><p class="drink-desc">Mango, apple, strawberry, coconut milk, vanilla yogurt, agave</p></div>
    <div class="drink"><p class="drink-name">Go Ape Glee</p><p class="drink-desc">Oats, banana, cinnamon, dates, almond butter</p></div>
    <div class="drink"><p class="drink-name">Caribbean Dream</p><p class="drink-desc">Pineapple, spinach, banana, coconut milk</p></div>
    <div class="drink"><p class="drink-name">Mocha Lotta</p><p class="drink-desc">Oats, banana, cinnamon, cocoa, espresso, skim milk</p></div>
    <div class="drink"><p class="drink-name">Cocoa Banana</p><p class="drink-desc">Oats, banana, cocoa, cinnamon, peanut butter , agave<br><span class="small-note">*Almond butter substitute is available</span></p></div>
    <div class="drink"><p class="drink-name">PB &amp; J Day</p><p class="drink-desc">Frozen berries, banana, peanut butter, maple syrup,<br>coconut milk <span class="small-note">*Spinach is optional</span></p></div>
    <div class="drink"><p class="drink-name">Strawberry Glee</p><p class="drink-desc">Strawberries, banana, coconut milk, orange juice, agave</p></div>
    <div class="drink"><p class="drink-name">Kale Krush</p><p class="drink-desc">Spinach, kale, pineapple, apple juice</p></div>
    <div class="drink"><p class="drink-name">Young Blood</p><p class="drink-desc">Celery, lemon, apple</p></div>
    <div class="drink"><p class="drink-name">Berry Beautiful</p><p class="drink-desc">Blueberries, banana, vanilla yogurt, soy milk,<br>collagen protein, agave,</p></div>
  </div>
</section>

<section class="abs panel shakes">
  <div class="shakes-band"><h2 class="shakes-title">SHAKES</h2></div>
  <p class="shakes-price">LARGE 20OZ £5.99 ADD PROTEIN FOR .50P</p>
  <div class="shake-grid">
    <div>
      <div class="shake"><p class="shake-name">Avo Shake</p><p class="shake-desc">Avocado, banana, skim milk, vanilla</p></div>
      <div class="shake"><p class="shake-name">Cocoa Shake</p><p class="shake-desc">Avocado, cocoa powder, coconut milk, banana, maple syrup<span class="small-note">*Can substitute avocado with dairy free ice cream</span></p></div>
      <div class="shake"><p class="shake-name">Sweet Vegan</p><p class="shake-desc">Dairy free vanilla Ice cream, banana, cocoa powder, coconut milk, agave</p></div>
    </div>
    <div>
      <div class="shake"><p class="shake-name">Caffeine Frenzy</p><p class="shake-desc">Espresso, banana, dairy free ice cream, cocoa powder, almond milk, agave</p></div>
      <div class="shake"><p class="shake-name">Berry Bunch</p><p class="shake-desc">Oats, mixed berries, banana, dates, soy milk, dairy free ice cream</p></div>
      <div class="shake"><p class="shake-name">The Last Straw</p><p class="shake-desc">Strawberry ,dates , dairy free ice cream, coconut milk, agave<span class="small-note">*Substitute dairy free ice cream for avocado</span></p></div>
    </div>
  </div>
</section>

<div class="abs yogurt">
  <p class="yogurt-name">YOGURT</p>
  <p class="price">£3</p>
  <p class="yogurt-desc">Coconut, vanilla yogurt,<br>banana, granola</p>
</div>

<section class="abs bowls">
  <h2 class="bowls-title">BOWLS</h2>
  <p class="bowls-protein">+ PROTEIN .50P</p>
  <p class="bowl-name">Acai Bowl</p>
  <p class="price">£4.50</p>
  <p class="bowl-desc">Acai, Raspberry,blueberry,banana,almond milk, granola</p>
  <p class="bowl-note">*Topping: granola and ½ banana sliced, chia seeds</p>
</section>

<section class="abs cocoa-bowl">
  <p class="bowl-name">Cocoa Bowl</p>
  <p class="price">£4.50</p>
  <p class="bowl-desc">Cocoa,banana,peanut butter,almond milk<br>*almond butter substitute is available</p>
  <p class="bowl-note">Toppings : chocolate granola, peanut butter ,chia seeds,1/2 banana sliced</p>
</section>

<section class="abs panel immune">
  <h2 class="immune-title">IMMUNE BOOSTERS</h2>
  <p class="immune-price">REGULAR 16OZ £6 SMOOTHIE BOWL £5.50</p>
  <p class="immune-note">*Available on a seasonal basis</p>
  <div class="immune-list">
    <div class="drink"><p class="drink-name">The Yellow One: Pineapple Turmeric</p><p class="drink-desc">Pineapple, banana, lemon, agave, ginger,tumeric,coconut water</p></div>
    <div class="drink"><p class="drink-name">The Red One : Citrus Berry Ginger</p><p class="drink-desc">Orange, strawberry, lemon, ginger , almond milk</p></div>
    <div class="drink"><p class="drink-name">The Orange One : Citrus Carrot</p><p class="drink-desc">Grapefruit, clementine, carrot, mango, yogurt, lemon, tumeric</p></div>
  </div>
</section>

<h2 class="abs sandwich-title">Glee Sandwiches</h2>

<div class="abs sandwich" style="left:44px;top:965px"><p class="sandwich-name">Avocado</p><p class="price">£4.50</p><p class="sandwich-desc">Avocado , mozerella, tomatoe, pesto</p></div>
<div class="abs sandwich" style="left:172px;top:965px"><p class="sandwich-name">Spicy Tuna</p><p class="price">£4.50</p><p class="sandwich-desc">Tuna, Chilli peppers, mayo, salt, pepper</p></div>
<div class="abs sandwich" style="left:300px;top:965px"><p class="sandwich-name">Tunacado</p><p class="price">£4.50</p><p class="sandwich-desc">Tuna, avocado, mayo, salt, pepper</p></div>
<div class="abs sandwich" style="left:44px;top:1053px"><p class="sandwich-name">BLT</p><p class="price">£4.50</p><p class="sandwich-desc">Turkey rasher, lettuce, mayo, tomatoe</p></div>
<div class="abs sandwich" style="left:172px;top:1046px;width:240px"><p class="sandwich-name">American Grilled Cheese</p><p class="price" style="margin-top:8px">£4.50</p><p class="sandwich-desc">Mature Cheddar ,<br>wholewheat bread</p><p class="sandwich-note">*sourdough bread is optional</p></div>

<section class="abs teas">
  <h2 class="teas-title">TEAS</h2>
  <p class="teas-price">REGULAR £2</p>
  <p class="tea">GREEN GEISHA</p>
  <p class="tea">BREAKFAST BLEND</p>
  <p class="tea">LEMON &amp; GINGER</p>
  <p class="tea">MOROCCAN MINT</p>
</section>

<section class="abs frap">
  <div class="frap-head">
    <h2 class="frap-title">ICED FRAPPÉ</h2>
    <p class="frap-price">REGULAR<br>£3.50</p>
  </div>
  <div class="frap-grid">
    <div>
      <p class="frap-name">CAPPUCCINO</p><p class="frap-desc">expresso, milk, ice</p>
      <p class="frap-name">MOCHA</p><p class="frap-desc">cocoa ,milk, ice</p>
      <p class="frap-name">STRAWBERRY'S N CREAM</p><p class="frap-desc">Strawberry,cream,ice</p>
    </div>
    <div>
      <p class="frap-name">MIGHTY MATCHA</p><p class="frap-desc">Matcha, cream, ice</p>
      <p class="frap-name">VANILLA BEAN</p><p class="frap-desc">Vanilla, cream, ice</p>
    </div>
  </div>
</section>
<div class="abs baseline"></div>

</body>
</html>
```